Copperleaf Roofing Business Card

This is my current business card. But I’d like to make some changes. Somewhere on the card I’d like to list some of the services we offer. Maybe on the back? But I’d still like to keep the red. White and black modern look.

-residential & commercial roofing
-Roof Repairs & Maintenance
-Storm Damage & Insurance Claims specialist
-Christmas Lights and permanent Christmas lights
Fencing. Windows. Gutters. Siding. Sheetrock, painting.

```html
<!DOCTYPE html>
<html lang="en">
<head>
<meta charset="utf-8">
<title>Copperleaf Roofing Co. – Business Card</title>
<link href="https://fonts.googleapis.com/css2?family=Montserrat:wght@400;500;700&family=Orbitron:wght@700;800&display=swap" rel="stylesheet">
<style>
  :root {
    --backdrop: #d8d1c6;
    --card: #1e1e1e;
    --red: #e3262c;
    --red-deep: #8f1418;
    --white: #ffffff;
    --muted: #e6e6e6;
  }
  * { margin: 0; padding: 0; box-sizing: border-box; }
  html, body { width: 900px; height: 1200px; overflow: hidden; }
  body {
    background: var(--backdrop);
    position: relative;
    font-family: "Montserrat", Arial, sans-serif;
    color: var(--white);
  }
  .card {
    position: absolute;
    left: 80px;
    width: 742px;
    height: 442px;
    background: var(--card);
    border-radius: 22px;
    overflow: hidden;
    box-shadow: 0 10px 24px rgba(0,0,0,.35);
  }
  .card--front { top: 130px; }
  .card--back { top: 638px; }
  .card__band {
    position: absolute;
    left: 0; right: 0; bottom: 0;
    height: 20px;
    background: linear-gradient(90deg, var(--red-deep), var(--red) 25%, var(--red-deep) 50%, var(--red) 75%, var(--red-deep));
  }
  .brand { position: absolute; left: 0; right: 0; text-align: center; }
  .brand__mark {
    display: block;
    margin: 0 auto;
    border-radius: 50%;
    background: var(--red);
    border: 4px solid var(--white);
  }
  .brand__name {
    display: block;
    font-family: "Montserrat", Arial, sans-serif;
    font-weight: 700;
    color: var(--red);
    text-transform: uppercase;
    letter-spacing: 1px;
    line-height: 1.1;
  }
  .card--front .brand { top: 22px; }
  .card--front .brand__mark { width: 118px; height: 118px; }
  .card--front .brand__name { font-size: 28px; margin-top: 16px; }
  .card--back .brand { top: 58px; }
  .card--back .brand__mark { width: 192px; height: 192px; }
  .card--back .brand__name { font-size: 44px; margin-top: 32px; }

  .services {
    position: absolute;
    top: 244px;
    right: 392px;
    list-style: none;
    text-align: right;
    font-size: 15px;
    line-height: 18px;
  }
  .services li { position: relative; padding-right: 14px; margin-bottom: 4px; }
  .services li::after {
    content: "";
    position: absolute;
    right: 0; top: 6px;
    width: 6px; height: 6px;
    border-radius: 50%;
    background: var(--red);
  }
  .divider {
    position: absolute;
    left: 364px; top: 248px;
    width: 2px; height: 152px;
    background: var(--red);
  }
  .contact { position: absolute; left: 376px; top: 250px; }
  .contact__name {
    font-family: "Orbitron", Arial, sans-serif;
    font-weight: 800;
    font-size: 24px;
    letter-spacing: 1px;
    text-transform: uppercase;
  }
  .contact__name .accent { color: var(--red); }
  .contact__role { font-size: 16px; color: var(--muted); margin-top: 4px; }
  .contact__list { list-style: none; margin-top: 10px; font-size: 16px; }
  .contact__list li { display: flex; align-items: center; gap: 9px; height: 28px; }
  .contact__list svg { width: 14px; height: 14px; fill: var(--red); flex: none; }
</style>
</head>
<body>

<section class="card card--front" aria-label="Business card front">
  <div class="brand">
    <span class="brand__mark"></span>
    <span class="brand__name">Copperleaf<br>Roofing Co.</span>
  </div>

  <ul class="services">
    <li>residential &amp; commercial roofing</li>
    <li>Roof Repairs &amp; Maintenance</li>
    <li>Storm Damage &amp;<br>Insurance Claims specialist</li>
    <li>Christmas Lights and<br>permanent Christmas lights</li>
    <li>Fencing. Windows. Gutters.<br>Siding. Sheetrock, painting</li>
  </ul>

  <span class="divider"></span>

  <div class="contact">
    <p class="contact__name">Dana <span class="accent">Whitfield</span></p>
    <p class="contact__role">Owner</p>
    <ul class="contact__list">
      <li>
        <svg viewBox="0 0 24 24" aria-hidden="true"><path d="M6.6 10.8a15 15 0 0 0 6.6 6.6l2.2-2.2a1 1 0 0 1 1-.25 11.4 11.4 0 0 0 3.6.57 1 1 0 0 1 1 1V20a1 1 0 0 1-1 1A17 17 0 0 1 3 4a1 1 0 0 1 1-1h3.5a1 1 0 0 1 1 1c0 1.25.2 2.45.57 3.57a1 1 0 0 1-.25 1z"/></svg>
        555-014-2290
      </li>
      <li>
        <svg viewBox="0 0 24 24" aria-hidden="true"><path d="M2 5h20v14H2z"/><path d="M3 6.5l9 7 9-7V6H3z" fill="#1e1e1e"/></svg>
        dana@copperleafroofing.com
      </li>
      <li>
        <svg viewBox="0 0 24 24" aria-hidden="true"><path d="M12 2a10 10 0 1 0 0 20 10 10 0 0 0 0-20zm6.9 6h-3a15.6 15.6 0 0 0-1.4-3.6A8 8 0 0 1 18.9 8zM12 4c.8 1.2 1.5 2.5 1.9 4h-3.8c.4-1.5 1.1-2.8 1.9-4zM4.3 14a8.2 8.2 0 0 1 0-4h3.4a16.5 16.5 0 0 0 0 4zm.8 2h3a15.6 15.6 0 0 0 1.4 3.6A8 8 0 0 1 5.1 16zm3-8h-3a8 8 0 0 1 4.4-3.6A15.6 15.6 0 0 0 8.1 8zM12 20c-.8-1.2-1.5-2.5-1.9-4h3.8c-.4 1.5-1.1 2.8-1.9 4zm2.3-6H9.7a14.7 14.7 0 0 1 0-4h4.6a14.7 14.7 0 0 1 0 4zm.2 5.6a15.6 15.6 0 0 0 1.4-3.6h3a8 8 0 0 1-4.4 3.6zm1.8-5.6a16.5 16.5 0 0 0 0-4h3.4a8.2 8.2 0 0 1 0 4z"/></svg>
        www.copperleafroofing.com
      </li>
    </ul>
  </div>

  <span class="card__band"></span>
</section>

<section class="card card--back" aria-label="Business card back">
  <div class="brand">
    <span class="brand__mark"></span>
    <span class="brand__name">Copperleaf<br>Roofing Co.</span>
  </div>
  <span class="card__band"></span>
</section>

</body>
</html>
```